Theater Ad

A graphic for advertising in an indoor theater.
Target Market(s)
Parents of infants, toddlers, tweens and teens.
Industry/Entity Type
Pediatric Ophthalmology
Font styles to use
Sans Serif
Colors
EB3D1F
EC4F4E
F09395
F8D3D4
FCEDEE
Requirements
Must have
- Use the copy, color scheme, and photos shown in the attached older billboard advertisement, but in a new design for the theater.

Nice to have
- New design with both logos included

Should not have
- Just a single logo - must include both logos

```html
<!DOCTYPE html>
<html lang="en">
<head>
<meta charset="UTF-8">
<title>Theater Ad – Pediatric Ophthalmology</title>
<link href="https://fonts.googleapis.com/css2?family=Poppins:wght@600;700;800&display=swap" rel="stylesheet">
<style>
  :root{
    --bg:#4a4a4a;
    --red:#c0001a;
    --red-line:#d9404f;
    --blue:#0a72bb;
    --white:#ffffff;
    --ink:#2b2b2b;
    --photo-a:#5c6b4a;
    --photo-b:#a89a88;
  }
  *{margin:0;padding:0;box-sizing:border-box}
  html,body{width:845px;height:1200px;overflow:hidden;background:var(--bg);font-family:"Poppins",sans-serif}
  .ad{position:absolute;left:20px;top:374px;width:805px;height:452px;background:var(--white);box-shadow:0 4px 14px rgba(0,0,0,.35)}
  .photo{position:absolute;left:0;top:0;width:308px;height:217px;background:linear-gradient(120deg,var(--photo-a),var(--photo-b))}
  .doctor{position:absolute;left:0;top:217px;width:308px;height:151px;background:var(--blue);color:var(--white);text-align:center;padding-top:22px}
  .doctor-name{font-size:23px;font-weight:700;line-height:1.1}
  .doctor-degree{font-size:15px;font-weight:700;margin-top:2px}
  .doctor-role{font-size:13.5px;font-weight:600;line-height:1.4;margin-top:10px}
  .credentials{position:absolute;left:308px;top:0;width:238px;height:368px;background:var(--red);color:var(--white);text-align:center}
  .credential{position:absolute;left:0;width:100%;display:flex;flex-direction:column;align-items:center}
  .credential + .credential{border-top:1px solid var(--red-line)}
  .credential svg{width:28px;height:28px}
  .credential-small{font-size:19px;font-weight:800;line-height:1;margin-top:6px}
  .credential-big{font-size:37px;font-weight:800;line-height:1}
  .c1{top:0;height:127px;padding-top:20px}
  .c2{top:127px;height:122px;padding-top:10px}
  .c3{top:249px;height:119px;padding-top:10px}
  .c3 .credential-big{font-size:40px}
  .side{position:absolute;left:546px;top:0;width:259px;height:368px;text-align:center}
  .spanish{font-size:21px;font-weight:700;color:var(--ink);margin-top:28px}
  .brand{display:flex;align-items:center;justify-content:center;gap:8px;font-size:19px;font-weight:800;color:var(--blue);line-height:1.1;text-align:left}
  .brand-dot{width:14px;height:14px;border-radius:50%;background:var(--blue);flex:none}
  .brand-1{margin-top:34px}
  .brand-2{margin-top:38px}
  .tagline{font-size:26px;font-weight:800;color:var(--ink);line-height:1.05;margin-top:44px}
  .contact{position:absolute;left:0;top:368px;width:100%;height:84px;display:flex;align-items:center;justify-content:center;gap:24px}
  .contact-item{display:flex;align-items:center;gap:8px;color:var(--ink);font-weight:700}
  .phone{font-size:33px}
  .web{font-size:23px}
  .web .hl-blue{color:var(--blue)}
  .web .hl-red{color:var(--red)}
</style>
</head>
<body>
<main class="ad">
  <div class="photo" role="img" aria-label="Portrait photo of the pediatric ophthalmologist in an office with plants"></div>
  <section class="doctor">
    <h1 class="doctor-name">Marina Kovalenko</h1>
    <p class="doctor-degree">M.D, M.P.H.</p>
    <p class="doctor-role">Pediatric Opthalmologist<br>Oftalmologia Pediatrica</p>
  </section>

  <section class="credentials">
    <div class="credential c1">
      <svg viewBox="0 0 28 28"><circle cx="14" cy="14" r="11.5" fill="none" stroke="var(--blue)" stroke-width="2.5"/><path d="M8 14l5 5 10-12" fill="none" stroke="var(--white)" stroke-width="3" stroke-linecap="round" stroke-linejoin="round"/></svg>
      <span class="credential-small">U.S. Residency</span>
      <span class="credential-big">Trained</span>
    </div>
    <div class="credential c2">
      <svg viewBox="0 0 28 28"><circle cx="14" cy="14" r="11.5" fill="none" stroke="var(--blue)" stroke-width="2.5"/><path d="M8 14l5 5 10-12" fill="none" stroke="var(--white)" stroke-width="3" stroke-linecap="round" stroke-linejoin="round"/></svg>
      <span class="credential-small">U.S. Fellowship</span>
      <span class="credential-big">Trained</span>
    </div>
    <div class="credential c3">
      <svg viewBox="0 0 28 28"><circle cx="14" cy="14" r="11.5" fill="none" stroke="var(--blue)" stroke-width="2.5"/><path d="M8 14l5 5 10-12" fill="none" stroke="var(--white)" stroke-width="3" stroke-linecap="round" stroke-linejoin="round"/></svg>
      <span class="credential-small">American Board</span>
      <span class="credential-big">Certified</span>
    </div>
  </section>

  <section class="side">
    <p class="spanish">Se Habla Español</p>
    <div class="brand brand-1"><span class="brand-dot"></span><span>Bright Sight<br>Eye Clinic</span></div>
    <div class="brand brand-2"><span class="brand-dot"></span><span>Bright Sight<br>Optical</span></div>
    <p class="tagline">“WE HELP KIDS<br>SEE BETTER!”</p>
  </section>

  <footer class="contact">
    <div class="contact-item phone">
      <svg width="24" height="24" viewBox="0 0 24 24"><path d="M6.6 10.8c1.4 2.8 3.8 5.1 6.6 6.6l2.2-2.2c.3-.3.7-.4 1-.2 1.1.4 2.3.6 3.6.6.6 0 1 .4 1 1V20c0 .6-.4 1-1 1C10.6 21 3 13.4 3 4c0-.6.4-1 1-1h3.5c.6 0 1 .4 1 1 0 1.3.2 2.5.6 3.6.1.3 0 .7-.2 1z" fill="var(--blue)"/></svg>
      <span>(555) 014-2870</span>
    </div>
    <div class="contact-item web">
      <svg width="22" height="22" viewBox="0 0 24 24" fill="none" stroke="var(--blue)" stroke-width="2"><circle cx="12" cy="12" r="10"/><ellipse cx="12" cy="12" rx="4.5" ry="10"/><path d="M2 12h20M4 6.5h16M4 17.5h16"/></svg>
      <span>www.<span class="hl-blue">brightsight</span><span class="hl-red">kids</span>.com</span>
    </div>
  </footer>
</main>
</body>
</html>
```